RW Holloway LLC Business Card - Civil Engineering & Consulting Firm

We need a Business Card that is elegant, and masculine.  It is our Professional Civil Engineering & Consulting Company located in San Antonio TX (Not s construction or builder firm- no gears & no tool images please). We provide civil engineering services including  commercial site plans, grading and drainage plans, utility plans, hydraulics and hydrology, land planning, utility coordination, and other general civil engineering services related to commercial and residential development.
We have 2 existing Logos. We would like to convey reliability, strength, trustworthiness and attention to detail.  Blues and orange tones as per logo We are OK with the use of a darker blue in the mix.  We have 2 logo versions - Full Company Name Logo to go on the back of card, & Small Icon Logo for the front w/ personal Info.

Target Market(s)
Architects, Real Estate Developers, Other Strctural Engineers, Surveyers, General Contractors
Industry/Entity Type
Professional Civil Engineering
Contact Information for Business Card
Name, Position, Address, Cell & Office #, email, and company website
Font styles to use
Other font styles liked:
- Avian
Requirements
Should not have
- No Tools, No Gears, no Cranes, or Construction Equipment.

```html
<!DOCTYPE html>
<html lang="en">
<head>
<meta charset="utf-8">
<title>RW Holloway LLC Business Card</title>
<link rel="stylesheet" href="https://fonts.googleapis.com/css2?family=Montserrat:wght@400;500;700&display=swap">
<style>
  :root {
    --stage: #d9d9d9;
    --sky: #78acdb;
    --amber: #e4913c;
    --paper: #eeeeef;
    --paper-shade: #e2e2e4;
    --paper-light: #f7f7f8;
    --ink: #1c1c1c;
    --white: #ffffff;
  }
  * { margin: 0; padding: 0; box-sizing: border-box; }
  html, body { width: 1200px; height: 900px; overflow: hidden; }
  body {
    background: var(--stage);
    font-family: "Montserrat", sans-serif;
    position: relative;
  }
  .card {
    position: absolute;
    left: 320px;
    width: 560px;
    height: 320px;
    border-radius: 22px;
    overflow: hidden;
    box-shadow: 0 6px 18px rgba(0,0,0,.18);
  }
  .card--front {
    top: 100px;
    background: linear-gradient(160deg, var(--sky) 0%, #a9aab0 48%, var(--amber) 85%);
    display: flex;
    align-items: center;
    justify-content: center;
  }
  .brand-name {
    color: var(--white);
    font-size: 40px;
    font-weight: 500;
    letter-spacing: 3px;
  }
  .card--back { top: 480px; background: var(--paper); }
  .facets { position: absolute; inset: 0; }
  .brand-mark {
    position: absolute;
    left: 195px;
    top: 196px;
    display: flex;
    align-items: center;
    gap: 8px;
    color: var(--amber);
    font-size: 14px;
    font-weight: 700;
    letter-spacing: .5px;
    white-space: nowrap;
  }
  .brand-mark__square { width: 10px; height: 10px; background: var(--amber); flex: none; }
  .person { position: absolute; left: 40px; bottom: 48px; }
  .person__name {
    color: var(--amber);
    font-size: 22px;
    font-weight: 700;
    letter-spacing: .5px;
  }
  .person__role { color: var(--ink); font-size: 15px; margin-top: 4px; }
  .contact {
    position: absolute;
    left: 350px;
    top: 42px;
    color: var(--ink);
    font-size: 12px;
    line-height: 1.35;
    white-space: nowrap;
  }
  .contact__address { margin-bottom: 16px; }
  .contact__list { list-style: none; }
  .contact__item { display: flex; align-items: center; gap: 8px; margin-bottom: 5px; }
  .contact__icon { width: 13px; height: 13px; flex: none; }
</style>
</head>
<body>
  <section class="card card--front" aria-label="Card back with company name">
    <div class="brand-name">RW Holloway LLC</div>
  </section>

  <section class="card card--back" aria-label="Card front with personal details">
    <svg class="facets" viewBox="0 0 560 320" preserveAspectRatio="none" aria-hidden="true">
      <polygon points="0,0 200,0 120,320 0,320" fill="var(--paper-shade)"/>
      <polygon points="200,0 340,0 260,320 120,320" fill="var(--paper-light)"/>
      <polygon points="420,0 560,0 560,200" fill="var(--paper-shade)"/>
      <polygon points="0,180 300,320 0,320" fill="var(--paper-light)"/>
    </svg>

    <div class="brand-mark"><span class="brand-mark__square"></span>RW Holloway LLC</div>

    <div class="person">
      <div class="person__name">DANE WHITFORD</div>
      <div class="person__role">Co-Founder</div>
    </div>

    <div class="contact">
      <p class="contact__address">4810 Alamo Ridge Drive<br>Suite 210 San Antonio</p>
      <ul class="contact__list">
        <li class="contact__item">
          <svg class="contact__icon" viewBox="0 0 16 16"><path d="M3 1l3 3-2 2c1 2 3 4 5 5l2-2 3 3-2 3C6 15 1 10 1 3z" fill="var(--amber)"/></svg>
          555-210-0148
        </li>
        <li class="contact__item">
          <svg class="contact__icon" viewBox="0 0 16 16"><rect x="2" y="6" width="12" height="8" rx="1" fill="var(--amber)"/><rect x="1" y="2" width="14" height="3" rx="1.5" fill="var(--amber)"/></svg>
          555-210-0392
        </li>
        <li class="contact__item">
          <svg class="contact__icon" viewBox="0 0 16 16"><rect x="1" y="3" width="14" height="10" fill="var(--amber)"/><path d="M1 3l7 6 7-6" fill="none" stroke="var(--white)" stroke-width="1.3"/></svg>
          info@rwholloway.example
        </li>
        <li class="contact__item">
          <svg class="contact__icon" viewBox="0 0 16 16"><circle cx="8" cy="8" r="7" fill="var(--amber)"/><path d="M1 8h14M8 1c-3 4-3 10 0 14M8 1c3 4 3 10 0 14" fill="none" stroke="var(--white)" stroke-width="1"/></svg>
          www.hollowaycivil.example
        </li>
      </ul>
    </div>
  </section>
</body>
</html>
```